Business Card Design needed for start up company Halvora

In need of a new business card designed for a start up company based in Sydney, Halvora is a new start up innovative Company, our mission it to make property accessible for everyday Australian and to become the leading Real Estate platform in Australia. We want it to be fresh and clean.

Industry/Entity Type

Financial

Contact Information for Business Card

Section for Name
Section for Title

HALVORA - The Strength of Pooling
Mobile:
Direct:

Font styles to use
Sans Serif

Colors
33a6d7
0692cd
0255a3
ffffff

Requirements
Must have
• Logo, all business card details

```html
<!DOCTYPE html>
<html lang="en">
<head>
<meta charset="utf-8">
<title>Halvora – Business Card</title>
<link href="https://fonts.googleapis.com/css2?family=Open+Sans:wght@400;600;700;800&display=swap" rel="stylesheet">
<style>
  :root {
    --sky: #33a6d7;
    --azure: #0692cd;
    --navy: #0255a3;
    --deep-navy: #163a70;
    --white: #ffffff;
    --backdrop: #2b2c2e;
    --paper: #f7f8f9;
  }
  * { box-sizing: border-box; margin: 0; padding: 0; }
  html, body {
    width: 1200px; height: 960px; overflow: hidden;
    background: var(--backdrop);
    font-family: "Open Sans", Arial, sans-serif;
  }
  .canvas { position: relative; width: 1200px; height: 960px; }
  .card {
    position: absolute; left: 250px; width: 700px; height: 400px;
    border-radius: 6px; overflow: hidden;
    box-shadow: 0 14px 30px rgba(0,0,0,.45);
  }

  /* Back of card */
  .card-back {
    top: 50px;
    background: linear-gradient(135deg, var(--azure) 0%, var(--sky) 100%);
    display: flex; flex-direction: column; align-items: center; justify-content: center;
  }
  .brand { display: flex; align-items: center; gap: 14px; }
  .brand-dot { border-radius: 50%; flex: none; }
  .brand-name { font-weight: 800; letter-spacing: 1px; line-height: 1; }
  .card-back .brand-dot { width: 66px; height: 66px; background: var(--white); }
  .card-back .brand-name { font-size: 68px; color: var(--white); }
  .tagline {
    margin-top: 42px; font-size: 15px; color: var(--white); letter-spacing: .3px;
  }

  /* Front of card */
  .card-front { top: 510px; background: var(--paper); }
  .wave { position: absolute; inset: 0; width: 700px; height: 400px; }
  .card-front .brand { position: absolute; top: 66px; right: 50px; }
  .card-front .brand-dot { width: 64px; height: 64px; background: var(--sky); }
  .card-front .brand-name { font-size: 60px; color: var(--navy); }

  .contact {
    position: absolute; left: 36px; top: 178px;
    color: var(--white); font-size: 15px; line-height: 22px; list-style: none;
  }
  .contact li { display: flex; align-items: center; gap: 8px; }
  .contact .address { padding-left: 22px; }
  .contact svg { width: 14px; height: 14px; flex: none; fill: var(--white); }

  .person { position: absolute; right: 42px; bottom: 28px; text-align: right; }
  .person-name { font-size: 19px; font-weight: 700; color: var(--sky); letter-spacing: .5px; }
  .person-title { font-size: 18px; font-weight: 400; color: var(--white); letter-spacing: .5px; }
</style>
</head>
<body>
<main class="canvas">

  <section class="card card-back" aria-label="Business card back">
    <div class="brand">
      <span class="brand-dot"></span>
      <span class="brand-name">HALVORA</span>
    </div>
    <p class="tagline">The Strength of Pooling</p>
  </section>

  <section class="card card-front" aria-label="Business card front">
    <svg class="wave" viewBox="0 0 700 400" preserveAspectRatio="none" aria-hidden="true">
      <path d="M0,118 C170,92 300,180 420,240 C520,290 620,292 700,262 L700,400 L0,400 Z" fill="var(--sky)"/>
      <path d="M0,128 C170,104 300,192 420,252 C520,302 620,304 700,274 L700,400 L0,400 Z" fill="var(--white)"/>
      <path d="M0,134 C170,110 300,198 420,258 C520,308 620,310 700,280 L700,400 L0,400 Z" fill="var(--deep-navy)"/>
    </svg>

    <div class="brand">
      <span class="brand-dot"></span>
      <span class="brand-name">HALVORA</span>
    </div>

    <ul class="contact">
      <li class="address">214 Harbour Crest Road</li>
      <li class="address">Sydney, NSW 2000</li>
      <li>
        <svg viewBox="0 0 24 24"><path d="M6.6 10.8a15 15 0 0 0 6.6 6.6l2.2-2.2c.3-.3.7-.4 1-.2 1.1.4 2.3.6 3.6.6.6 0 1 .4 1 1V20c0 .6-.4 1-1 1C10.6 21 3 13.4 3 4c0-.6.4-1 1-1h3.5c.6 0 1 .4 1 1 0 1.3.2 2.5.6 3.6.1.3 0 .7-.2 1z"/></svg>
        0412 558 903
      </li>
      <li>
        <svg viewBox="0 0 24 24"><path d="M7 1h10a2 2 0 0 1 2 2v18a2 2 0 0 1-2 2H7a2 2 0 0 1-2-2V3a2 2 0 0 1 2-2zm0 3v14h10V4zm5 15.5a1 1 0 1 0 0 2 1 1 0 0 0 0-2z"/></svg>
        02 9184 3376
      </li>
      <li>
        <svg viewBox="0 0 24 24"><path d="M2 5h20v2l-10 6L2 7zm0 4 10 6 10-6v10H2z"/></svg>
        hello@halvora.au
      </li>
      <li>
        <svg viewBox="0 0 24 24"><circle cx="12" cy="12" r="10"/></svg>
        www.halvora.au
      </li>
    </ul>

    <div class="person">
      <p class="person-name">MARA ELLISON</p>
      <p class="person-title">CEO/FOUNDER</p>
    </div>
  </section>

</main>
</body>
</html>
```